Advertisement Design

I'm looking for a post card sized advertisement piece that I will be dropping off to commercial and residential customers.
On one side I want it promoting carpet cleaning services and on the other side dryer vent cleaning services.
I've uploaded two different layouts of my company logo for you to choice from.
One batch will be printed with my Michigan Number
One batch will be printed with my Tennessee number
Will share contact numbers with the winner so just use a make up number
742-318-9516

```html
<!DOCTYPE html>
<html lang="en">
<head>
<meta charset="utf-8">
<title>Larkfield Postcards</title>
<link href="https://fonts.googleapis.com/css2?family=Poppins:wght@400;500;600;700&display=swap" rel="stylesheet">
<style>
:root{
  --bg:#a1a1a1;
  --blue:#0b79c0;
  --cyan:#1ea6e2;
  --navy:#0a2236;
  --label:#4a4a4a;
  --white:#ffffff;
}
*{margin:0;padding:0;box-sizing:border-box}
html,body{width:674px;height:1200px;overflow:hidden;background:var(--bg)}
body{position:relative;font-family:'Poppins',sans-serif}
.card{position:absolute;left:27px;width:620px;height:414px;background:var(--white);overflow:hidden;box-shadow:0 3px 8px rgba(0,0,0,.3)}
.card--carpet{top:166px}
.card--vent{top:620px}
.abs{position:absolute}
.dark-zone{background:var(--navy)}
.ghost-photo{background:linear-gradient(90deg,rgba(255,255,255,0) 0%,#e9ebee 45%,#dfe2e6 100%)}
.photo-frame{background:linear-gradient(180deg,var(--cyan),var(--blue))}
.photo{background:radial-gradient(ellipse at 55% 70%,#8a857c 0%,#6f6a62 40%,#c9cbcf 75%,#e3e5e8 100%)}
.photo--vent{background:linear-gradient(135deg,#e6e8ea 0%,#c7ccd1 30%,#5d8fc7 55%,#2c64b4 75%,#1b4ea3 100%)}
.brand-title{font-family:'Poppins',sans-serif;font-weight:700;font-size:50px;line-height:56px;letter-spacing:1px;color:var(--blue);white-space:nowrap}
.service-name{font-family:'Poppins',sans-serif;font-weight:700;font-size:17px;letter-spacing:3.6px;color:var(--navy);line-height:1}
.intro-band{background:var(--blue);border-radius:0 10px 10px 0;color:var(--white);font-weight:600;font-size:8.6px;line-height:10.6px;padding:6px 0 0 35px}
.body-copy{color:var(--white);font-size:8.9px;line-height:11.2px;border-left:3px solid var(--blue);padding-left:8px}
.supplies-heading{color:var(--cyan);font-weight:700;font-size:11.6px;line-height:14px}
.icon-item{position:absolute;width:96px;margin-left:-48px;text-align:center;top:279px}
.icon-item svg{display:block;margin:0 auto}
.icon-label{color:var(--label);font-weight:600;font-size:8.3px;line-height:10px;margin-top:1px}
.region-heading{color:var(--blue);font-weight:700;font-size:9.6px}
.region-copy{color:var(--label);font-size:7.4px;line-height:9px;margin-top:2px}
.logo{left:32px;top:353px;height:46px;display:flex;align-items:center;gap:8px}
.logo-square{width:22px;height:22px;background:var(--blue)}
.logo-rule{width:1.5px;height:46px;background:var(--navy)}
.logo-name{font-family:'Poppins',sans-serif;font-weight:500;font-size:12.5px;color:var(--blue);letter-spacing:.5px}
.phone{left:187px;top:360px;display:flex;align-items:center;gap:2px;font-weight:600;font-size:16.5px;color:var(--navy)}
.web-bar{left:358px;top:357px;width:262px;height:27px;background:var(--navy);border-radius:6px 0 0 6px;color:var(--white);font-weight:500;font-size:14px;letter-spacing:1.4px;line-height:27px;padding-left:22px;box-shadow:0 5px 6px -3px rgba(0,0,0,.35);white-space:nowrap}
.web-bar .domain{color:var(--cyan)}
</style>
</head>
<body>

<svg width="0" height="0" style="position:absolute">
  <defs>
    <symbol id="ring" viewBox="0 0 34 34"><circle cx="17" cy="17" r="15.5" fill="#fff" stroke="#0b79c0" stroke-width="2.6"/></symbol>
  </defs>
</svg>

<section class="card card--carpet">
  <div class="abs ghost-photo" style="left:130px;top:0;width:215px;height:170px" role="img" aria-label="Faded photo of a man vacuuming a room"></div>
  <div class="abs dark-zone" style="left:0;top:183px;width:620px;height:110px"></div>
  <div class="abs photo-frame" style="left:343px;top:0;width:277px;height:262px;border-radius:0 0 0 26px"></div>
  <div class="abs photo" style="left:355px;top:0;width:265px;height:250px;border-radius:0 0 0 20px" role="img" aria-label="Photo of a vacuum cleaner head on a shaggy carpet"></div>

  <div class="abs brand-title" style="left:32px;top:72px">LARKFIELD</div>
  <div class="abs service-name" style="left:34px;top:139px">CARPET CLEANING</div>

  <div class="abs intro-band" style="left:0;top:166px;width:327px;height:34px">After decades of experience, we’ve perfected a carpet cleaning process that provides beautiful results for our clients.</div>

  <p class="abs body-copy" style="left:37px;top:219px;width:300px">We have been providing Carpet Cleaning Services for 40 years. With state-of-the-art industrial equipment &amp; out years of experience there is not mush we cannot get clean. Carpet&nbsp; Cleaning Services include the following.</p>

  <div class="icon-item" style="left:68px"><svg width="34" height="34" viewBox="0 0 34 34"><use href="#ring"/><rect x="11" y="10" width="12" height="14" rx="6" fill="none" stroke="#0b79c0" stroke-width="2" transform="rotate(35 17 17)"/></svg><div class="icon-label">Industrial Carpet<br>Cleaning</div></div>
  <div class="icon-item" style="left:159px"><svg width="34" height="34" viewBox="0 0 34 34"><use href="#ring"/><circle cx="14" cy="20" r="4" fill="none" stroke="#0b79c0" stroke-width="2"/><path d="M17 17l6-7" stroke="#0b79c0" stroke-width="3"/></svg><div class="icon-label">Residential Carpet<br>Cleaning</div></div>
  <div class="icon-item" style="left:249px"><svg width="34" height="34" viewBox="0 0 34 34"><use href="#ring"/><rect x="11" y="9" width="12" height="16" fill="none" stroke="#0b79c0" stroke-width="2"/><path d="M14 13h6M14 17h6M14 21h6" stroke="#0b79c0" stroke-width="1.5"/></svg><div class="icon-label">Rug<br>Cleaning</div></div>
  <div class="icon-item" style="left:344px"><svg width="34" height="34" viewBox="0 0 34 34"><use href="#ring"/><path d="M8 19h18l-4 5H11z" fill="#0b79c0"/><path d="M13 19v-5h7l3 5" fill="none" stroke="#0b79c0" stroke-width="1.6"/></svg><div class="icon-label">Boat, RV, Private Plane<br>Carpet Cleaning</div></div>
  <div class="icon-item" style="left:446px"><svg width="34" height="34" viewBox="0 0 34 34"><use href="#ring"/><rect x="12" y="9" width="10" height="4" fill="#0b79c0"/><rect x="13" y="14" width="8" height="6" fill="#0b79c0"/><rect x="15.5" y="20" width="3" height="6" fill="#0b79c0"/></svg><div class="icon-label">Tile &amp; Grout steam<br>cleaning / sealing</div></div>
  <div class="icon-item" style="left:546px"><svg width="34" height="34" viewBox="0 0 34 34"><use href="#ring"/><path d="M8 16q9-9 18 0z" fill="#0b79c0"/><path d="M17 16v10M11 26l2-6h8l2 6" stroke="#0b79c0" stroke-width="1.6" fill="none"/></svg><div class="icon-label">Corridor &amp; Outdoor<br>Carpet Cleaning</div></div>

  <div class="abs logo"><span class="logo-square"></span><span class="logo-rule"></span><span class="logo-name">LARKFIELD</span></div>
  <div class="abs phone"><svg width="16" height="16" viewBox="0 0 16 16"><circle cx="8" cy="8" r="7.5" fill="#0b79c0"/><path d="M5 4.5c.6-.5 1.2-.3 1.5.3l.6 1.3c.2.4 0 .8-.3 1-.3.2-.3.5-.1.8.5.8 1.1 1.4 1.9 1.9.3.2.6.2.8-.1.2-.3.6-.5 1-.3l1.3.6c.6.3.8.9.3 1.5-.8.9-2 .9-3.2.2C7 10.9 5.1 9 4.3 7.4c-.6-1.1-.2-2.2.7-2.9z" fill="#fff"/></svg>(742) 318-9516</div>
  <div class="abs web-bar">www.<span class="domain">larkfieldclean</span>.com</div>
</section>

<section class="card card--vent">
  <div class="abs ghost-photo" style="left:400px;top:0;width:220px;height:160px" role="img" aria-label="Faded photo of a vent grille being cleaned"></div>
  <div class="abs dark-zone" style="left:0;top:167px;width:620px;height:122px"></div>
  <div class="abs photo-frame" style="left:0;top:0;width:273px;height:263px;border-radius:0 0 26px 0"></div>
  <div class="abs photo photo--vent" style="left:0;top:0;width:262px;height:252px;border-radius:0 0 20px 0" role="img" aria-label="Photo of a technician spray-cleaning an air unit"></div>

  <div class="abs brand-title" style="left:294px;top:69px">LARKFIELD</div>
  <div class="abs service-name" style="left:296px;top:136px">VENT CLEANING</div>

  <p class="abs body-copy" style="left:307px;top:183px;width:292px">A DIY dryer vent cleaning process shouldn’t take you more than an hour as long as you have the right info and tools. Here are seven simple steps that will get all that lint and gunk out of the hose attachment</p>

  <p class="abs supplies-heading" style="left:297px;top:238px;width:300px">Here are the cleaning products &amp; supplies you’ll need to get the job done</p>

  <div class="abs" style="left:32px;top:298px;width:250px">
    <div class="region-heading">We Serve The Lakeshore &amp; River Valley Areas</div>
    <div class="region-copy">We serve communities all across the region, including lakeside towns, river valley suburbs, the downtown core, nearby farm country and more.</div>
  </div>

  <div class="icon-item" style="left:318px;top:275px"><svg width="34" height="34" viewBox="0 0 34 34"><use href="#ring"/><path d="M10 23l5-9 7-3 2 4-5 5z" fill="#0b79c0"/></svg><div class="icon-label" style="font-size:8.6px">Cordless<br>vacuum</div></div>
  <div class="icon-item" style="left:398px;top:275px"><svg width="34" height="34" viewBox="0 0 34 34"><use href="#ring"/><circle cx="16" cy="17" r="7" fill="none" stroke="#0b79c0" stroke-width="2.4"/><circle cx="16" cy="17" r="2.5" fill="#0b79c0"/><path d="M16 24h9" stroke="#0b79c0" stroke-width="2"/></svg><div class="icon-label" style="font-size:8.6px">Electrical or<br>duct tape</div></div>
  <div class="icon-item" style="left:479px;top:275px"><svg width="34" height="34" viewBox="0 0 34 34"><use href="#ring"/><path d="M22 8l-5 11" stroke="#0b79c0" stroke-width="2"/><path d="M13 19h8l-2 6h-8z" fill="#0b79c0"/></svg><div class="icon-label" style="font-size:8.6px">Broom and<br>dustpan</div></div>
  <div class="icon-item" style="left:561px;top:275px"><svg width="34" height="34" viewBox="0 0 34 34"><use href="#ring"/><rect x="10" y="11" width="13" height="7" rx="3" fill="#0b79c0"/><rect x="13" y="18" width="4" height="8" fill="#0b79c0"/><path d="M23 14h3" stroke="#0b79c0" stroke-width="2"/></svg><div class="icon-label" style="font-size:8.6px">Dryer duct<br>cleaning kit</div></div>

  <div class="abs logo"><span class="logo-square"></span><span class="logo-rule"></span><span class="logo-name">LARKFIELD</span></div>
  <div class="abs phone"><svg width="16" height="16" viewBox="0 0 16 16"><circle cx="8" cy="8" r="7.5" fill="#0b79c0"/><path d="M5 4.5c.6-.5 1.2-.3 1.5.3l.6 1.3c.2.4 0 .8-.3 1-.3.2-.3.5-.1.8.5.8 1.1 1.4 1.9 1.9.3.2.6.2.8-.1.2-.3.6-.5 1-.3l1.3.6c.6.3.8.9.3 1.5-.8.9-2 .9-3.2.2C7 10.9 5.1 9 4.3 7.4c-.6-1.1-.2-2.2.7-2.9z" fill="#fff"/></svg>(742) 318-9516</div>
  <div class="abs web-bar">www.<span class="domain">larkfieldclean</span>.com</div>
</section>

</body>
</html>
```